Unique malt liquor beverage needs a logo design and bottle (6.9oz clear glass flask) label designed.

We need a logo and bottle label design for our new beverage here at Lofty Brewworks, a new company based in West Virginia. This is a differentiated product in that we use only natural ingredients and deliver it in a novel 6.9oz glass flask. Our new beverage is a naturally flavored malt liquor drink that we call "Glimmer". Our proposed tag line will be "Made to Glim" or "Cold Sip. Bold Glim". We want a logo and bottle label design that differentiates us even further.

Target Market(s)

See images I uploaded to see our two competitors...we need to be better than this but it gives you idea of the spirit of this beverage class.

Industry/Entity Type

Alcohol beverage

Requirements
Must have
• Label needs to include “14% alc/vol 6.9 oz” Both of these elements can be small and at bottom of front face of label. Also must look great on clear glass flask.
Should not have
• Do not put "malt liquor" on label. Under "Glimmer" name it will need to state "Alcoholic Beverage"

```html
<!DOCTYPE html>
<html lang="en">
<head>
<meta charset="utf-8">
<title>Glimmer Label</title>
<link href="https://fonts.googleapis.com/css2?family=Stint+Ultra+Condensed&family=Rye&family=Oswald:wght@400&family=Montserrat:wght@500;800&display=swap" rel="stylesheet">
<style>
  :root {
    --page: #ffffff;
    --navy: #0f2358;
    --navy-ink: #14275c;
    --frame: #6f80b3;
    --silver-light: #d4d5d8;
    --silver-dark: #bfc0c4;
    --wine: #7b2b2a;
    --wine-edge: #a7625e;
    --cream: #f3ece2;
    --white: #ffffff;
  }
  html, body {
    margin: 0;
    width: 1200px;
    height: 1200px;
    overflow: hidden;
    background: var(--page);
  }
  .canvas {
    position: relative;
    width: 1200px;
    height: 1200px;
  }
  .label {
    position: absolute;
    left: 255px;
    top: 60px;
    width: 690px;
    height: 1080px;
  }
  .label svg { display: block; }
  .brand-name {
    font-family: "Montserrat", sans-serif;
    font-weight: 800;
    font-size: 24px;
    letter-spacing: 5px;
    fill: var(--white);
  }
  .product-name {
    font-family: "Stint Ultra Condensed", serif;
    font-size: 330px;
    fill: var(--navy-ink);
  }
  .tagline {
    font-family: "Rye", serif;
    font-size: 36px;
    fill: var(--cream);
  }
  .category {
    font-family: "Rye", serif;
    font-size: 40px;
    fill: var(--white);
  }
  .flavor-note {
    font-family: "Montserrat", sans-serif;
    font-weight: 800;
    font-size: 22px;
    letter-spacing: 10px;
    fill: var(--white);
  }
  .origin {
    font-family: "Oswald", sans-serif;
    font-size: 44px;
    letter-spacing: 2px;
    fill: var(--white);
  }
  .spec {
    font-family: "Montserrat", sans-serif;
    font-weight: 500;
    font-size: 24px;
    fill: var(--white);
  }
</style>
</head>
<body>
<main class="canvas">
  <section class="label">
    <svg width="690" height="1080" viewBox="0 0 690 1080" xmlns="http://www.w3.org/2000/svg">
      <defs>
        <linearGradient id="silverBand" x1="0" y1="0" x2="1" y2="1">
          <stop offset="0" stop-color="var(--silver-dark)"/>
          <stop offset="0.5" stop-color="var(--silver-light)"/>
          <stop offset="1" stop-color="var(--silver-dark)"/>
        </linearGradient>
      </defs>

      <rect class="label-ground" x="0" y="0" width="690" height="1080" fill="var(--navy)"/>

      <path class="ornament-frame" role="img" aria-label="Border of leaf sprigs and dots around the label"
            fill="var(--frame)" fill-opacity="0.45" fill-rule="evenodd"
            d="M22 24 H668 V1056 H22 Z M72 78 V1002 H618 V78 Z"/>

      <polygon class="diagonal-band" points="0,329 690,215 690,604 0,699" fill="url(#silverBand)"/>

      <g class="maker-mark">
        <circle cx="180" cy="170" r="17" fill="var(--white)"/>
        <text class="brand-name" x="208" y="179">LOFTY BREWWORKS</text>
      </g>

      <text class="product-name" transform="translate(350 575) skewY(-9)" x="0" y="0"
            text-anchor="middle" textLength="500" lengthAdjust="spacingAndGlyphs">GLIMMER</text>

      <g class="tagline-box">
        <rect x="158" y="658" width="386" height="74" fill="var(--wine)" stroke="var(--wine-edge)" stroke-width="2"/>
        <text class="tagline" x="351" y="708" text-anchor="middle">MADE TO GLIM</text>
      </g>

      <text class="category" x="345" y="800" text-anchor="middle" textLength="480" lengthAdjust="spacingAndGlyphs">ALCOHOLIC BEVERAGE</text>

      <rect class="flourish" role="img" aria-label="Small scroll flourish" x="265" y="842" width="160" height="14" rx="7" fill="var(--frame)" fill-opacity="0.7"/>
      <text class="flavor-note" x="345" y="890" text-anchor="middle" textLength="450" lengthAdjust="spacing">NATURALLY FLAVORED</text>
      <rect class="flourish" role="img" aria-label="Small scroll flourish" x="265" y="916" width="160" height="14" rx="7" fill="var(--frame)" fill-opacity="0.7"/>

      <text class="spec" x="93" y="975">14%</text>
      <text class="spec" x="93" y="1000">alc/vol</text>
      <text class="origin" x="345" y="990" text-anchor="middle">WEST VIRGINIA</text>
      <text class="spec" x="584" y="975" text-anchor="end">6.9</text>
      <text class="spec" x="578" y="1000" text-anchor="end">oz</text>
    </svg>
  </section>
</main>
</body>
</html>
```